Telecommunications/Power civil contractor needs business card design

Were a new telecommunications/power underground civil contractor that is looking for a new business card design. Our company colours are silver or grey and orange. Feel free to use the white background logo or the black background logo.

Target Market(s)

Local contractors, utility companies, private sector mining/energy companies, developers.

Industry/Entity Type

Telecommunications

Contact Information for Business Card

Each card will need the following info:
Persons name:
Title:
E-mail:
Phone number:
Shop Address:
Mailing Address:

Requirements
Must have
• Each card will need the following info:
• Persons name:
• Title:
• E-mail:
• Phone number:
• Shop Address:
• Mailing Address:

```html
<!DOCTYPE html>
<html lang="en">
<head>
<meta charset="utf-8">
<title>Kestrel Underground Inc – Business Card</title>
<link href="https://fonts.googleapis.com/css2?family=Montserrat:wght@400;500;700;800&display=swap" rel="stylesheet">
<style>
  :root {
    --stage: #e9e6e1;
    --card: #0d0d0e;
    --card-edge: #1c1c1e;
    --orange: #f26a2e;
    --silver: #b9b9bc;
    --silver-dark: #6d6d72;
    --text: #f1f1f1;
  }
  * { margin: 0; padding: 0; box-sizing: border-box; }
  html, body {
    width: 1200px; height: 1022px; overflow: hidden;
    background: var(--stage);
    font-family: "Montserrat", sans-serif;
  }
  .stage {
    position: relative; width: 1200px; height: 1022px;
    display: flex; flex-direction: column; align-items: center; justify-content: center; gap: 62px;
  }
  .card {
    position: relative; width: 700px; height: 400px;
    background: linear-gradient(160deg, var(--card-edge) 0%, var(--card) 55%);
    border-radius: 22px; overflow: hidden;
    box-shadow: 0 18px 40px rgba(0,0,0,.28);
  }
  .card__swoosh { position: absolute; inset: 0; }

  /* back: contact side */
  .contact { position: absolute; left: 56px; top: 62px; color: var(--text); }
  .contact__name {
    color: var(--orange); font-weight: 500; font-size: 34px; letter-spacing: 1.5px; text-transform: uppercase;
  }
  .contact__title { font-size: 19px; margin-top: 4px; }
  .contact__address { font-size: 19px; line-height: 1.35; margin-top: 20px; }
  .contact__address + .contact__address { margin-top: 10px; }
  .contact__lines { list-style: none; margin-top: 18px; font-size: 19px; line-height: 1.45; }
  .contact__lines li { display: flex; align-items: center; gap: 14px; }
  .contact__icon { width: 18px; height: 18px; flex: none; }

  /* front: brand side */
  .brand {
    position: absolute; right: 60px; top: 50%; transform: translateY(-50%);
    display: flex; align-items: center; gap: 26px;
  }
  .brand__dot {
    width: 118px; height: 118px; border-radius: 50%;
    border: 8px solid var(--silver-dark);
  }
  .brand__name {
    color: var(--orange); font-weight: 800; font-size: 42px; line-height: 1.05; letter-spacing: 1px; text-transform: uppercase;
  }
</style>
</head>
<body>
<main class="stage">

  <section class="card card--back" aria-label="Business card, contact side">
    <svg class="card__swoosh" viewBox="0 0 700 400" aria-hidden="true">
      <path d="M430 -10 C 620 60, 700 250, 610 420" fill="none" stroke="var(--silver)" stroke-width="7"/>
      <path d="M458 -10 C 645 70, 720 255, 640 420" fill="none" stroke="var(--silver-dark)" stroke-width="4"/>
    </svg>
    <div class="contact">
      <h1 class="contact__name">Marlon Keane</h1>
      <p class="contact__title">Director</p>
      <p class="contact__address">48 Foundry Lane<br>Harlow Falls, NY 12604</p>
      <p class="contact__address">PO Box 3187<br>Reseda Park, CA 91522</p>
      <ul class="contact__lines">
        <li>
          <svg class="contact__icon" viewBox="0 0 18 18" aria-hidden="true"><rect x="4" y="1" width="10" height="16" rx="2" fill="none" stroke="var(--orange)" stroke-width="1.8"/><circle cx="9" cy="14" r="1" fill="var(--orange)"/></svg>
          +330 5182-4037
        </li>
        <li>
          <svg class="contact__icon" viewBox="0 0 18 18" aria-hidden="true"><path d="M4 1.5 L7 5 L5.2 7 C6.3 9.5 8.5 11.7 11 12.8 L13 11 L16.5 14 L14.5 16.5 C8 16 2 10 1.5 3.5 Z" fill="var(--orange)"/></svg>
          +330 6091-2845
        </li>
        <li>
          <svg class="contact__icon" viewBox="0 0 18 18" aria-hidden="true"><rect x="1.5" y="3.5" width="15" height="11" fill="none" stroke="var(--orange)" stroke-width="1.8"/><path d="M1.5 3.5 L9 10 L16.5 3.5" fill="none" stroke="var(--orange)" stroke-width="1.8"/></svg>
          hello@kestrelunderground.com
        </li>
        <li>
          <svg class="contact__icon" viewBox="0 0 18 18" aria-hidden="true"><circle cx="9" cy="9" r="7.5" fill="none" stroke="var(--orange)" stroke-width="1.6"/><ellipse cx="9" cy="9" rx="3.2" ry="7.5" fill="none" stroke="var(--orange)" stroke-width="1.4"/><path d="M1.5 9 H16.5" stroke="var(--orange)" stroke-width="1.4"/></svg>
          www.kestrelunderground.com
        </li>
      </ul>
    </div>
  </section>

  <section class="card card--front" aria-label="Business card, brand side">
    <svg class="card__swoosh" viewBox="0 0 700 400" aria-hidden="true">
      <path d="M-20 300 C 120 230, 230 300, 260 420" fill="none" stroke="var(--silver)" stroke-width="6" opacity=".55"/>
    </svg>
    <div class="brand">
      <span class="brand__dot" aria-hidden="true"></span>
      <p class="brand__name">Kestrel<br>Underground Inc</p>
    </div>
  </section>

</main>
</body>
</html>
```